Herbalist's Pain Cream WIX Website Redesign

I need a complete WIX website redesign! I am an herbalist and I'm relaunching my company, starting with a pain cream as the flagship product. My natural pain relief cream is composed of 6 active botanicals, uses all natural preservatives and provides pain relief within 1 minute! I have a new label design that reflects the high quality of this product and its ingredients. I have the content written and a rough website outline. I want the new website to match the color scheme of the label, and to show the quality of the product. (Logo uploaded is older color scheme. See New Label upload for updated color scheme.) I will be launching more products in the future, but the current content is for 1 flagship product. I want a high quality, earthy/ natural, botanical medicine feel. SEO phrase "Natural Pain Relief Cream" Old website is up again, for pictures: www.fennowroots.com

Target Market(s)

Middle to later aged women, Same for Men, but usually introduced by woman in their life

Industry/Entity Type

Botanical Supplement

Coding

Coded - Design and coding required

Number of Pages Required

5+ page

Colors
0054AA
0677BA
7BADD7
CADEEF
E8F1F8

Requirements
Must have
• Homepage, About, Ingredients, Shop, Contact Us
Nice to have
• FAQ section, maybe graphics to highlight unique elements

```html
<!DOCTYPE html>
<html lang="en">
<head>
<meta charset="utf-8">
<title>Fennow Roots Remedies — Mobile Website Screens</title>
<link href="https://fonts.googleapis.com/css2?family=DM+Sans:wght@400;500;700;800&family=Noto+Serif:wght@500;600&display=swap" rel="stylesheet">
<style>
  :root{
    --bg:#efeff1;
    --surface:#fafafa;
    --brand-blue:#0054aa;
    --blue-2:#0677ba;
    --blue-3:#7badd7;
    --blue-4:#cadeef;
    --blue-5:#e8f1f8;
    --navy:#14205a;
    --teal:#2fa3a6;
    --ink:#3b3f4a;
    --muted:#6b7080;
  }
  *{box-sizing:border-box;margin:0;padding:0}
  html,body{width:1200px;height:1200px;overflow:hidden}
  body{background:var(--bg);font-family:"DM Sans",sans-serif;color:var(--ink);position:relative}

  .brand{position:absolute;left:45px;top:80px;width:265px}
  .brand__row{display:flex;align-items:center;gap:12px}
  .brand__dot{width:32px;height:32px;border-radius:50%;background:var(--teal);flex:none}
  .brand__name{font-size:30px;font-weight:500;color:var(--teal);line-height:1;white-space:nowrap}
  .brand__tag{margin:12px 0 0 44px;font-size:15px;font-weight:500;color:var(--teal);letter-spacing:1.5px;white-space:nowrap}

  .screen{position:absolute;width:250px;background:var(--surface);border-radius:22px;overflow:hidden;
    box-shadow:0 18px 40px rgba(20,32,90,.10);display:flex;flex-direction:column}
  .pad{padding:20px 20px}
  .photo{width:100%}
  .eyebrow{font-size:11px;color:var(--navy);font-weight:500;margin-bottom:8px}
  .h-sans{font-size:21px;font-weight:800;color:var(--navy);line-height:1.22;margin-bottom:12px}
  .body-copy{font-size:9.5px;line-height:1.55;color:var(--ink)}
  .body-copy b{font-weight:700}
  .btn{display:inline-block;background:var(--brand-blue);color:#fff;font-size:11px;font-weight:500;
    padding:11px 22px;border-radius:4px;margin-top:14px}

  .faq{background:var(--brand-blue);color:#fff;padding:26px 20px;flex:1}
  .faq__eyebrow{display:flex;align-items:center;justify-content:flex-end;gap:8px;font-size:10px;opacity:.8}
  .faq__eyebrow span.rule{width:36px;height:2px;background:#fff}
  .faq__title{font-size:22px;font-weight:700;text-align:right;margin-top:6px}
  .faq__sub{font-size:9px;text-align:right;opacity:.75;margin-top:4px}
  .faq__item{border:1px solid rgba(255,255,255,.35);padding:12px;margin-top:12px;font-size:10.5px;font-weight:700;
    display:flex;justify-content:space-between;gap:8px}
  .faq__item p{font-weight:400;font-size:9px;line-height:1.5;opacity:.85;margin-top:8px}
  .faq__item .icon{font-weight:400;font-size:14px;line-height:1}

  .hero-title{font-family:"Noto Serif",serif;font-weight:600;font-size:22px;line-height:1.4;color:var(--navy)}
  .mini-brand{display:flex;align-items:center;gap:6px;font-size:11px;font-weight:500;color:var(--teal)}
  .mini-brand i{width:12px;height:12px;border-radius:50%;background:var(--teal);display:block}
  .menu{width:16px;height:9px;border-top:2px solid var(--brand-blue);border-bottom:2px solid var(--brand-blue)}

  .field{border:1px solid #e2e4ea;background:#fff;font-size:9.5px;color:var(--muted);padding:10px;margin-top:10px}
  .nav-list{list-style:none;font-size:10.5px;color:var(--ink);line-height:2.1}
  .nav-title{font-size:12px;font-weight:700;color:var(--navy);margin:18px 0 4px}
</style>
</head>
<body>

<div class="brand">
  <div class="brand__row">
    <span class="brand__dot"></span>
    <span class="brand__name">Fennow Roots</span>
  </div>
  <div class="brand__tag">HERBAL REMEDIES</div>
</div>

<!-- Column 1 -->
<section class="screen" style="left:45px;top:220px;height:500px">
  <div class="photo" role="img" aria-label="Product photo collage: white yarrow flowers, a jar of pain cream and a dropper bottle" style="height:190px;background:linear-gradient(135deg,#5d6b3f 0%,#b9c0b6 45%,#9aa3a8 60%,#d9c59a 100%)"></div>
  <div class="pad">
    <div class="eyebrow">Ingridients</div>
    <h2 class="h-sans">We use herbs harvested from the wild and from the farm, to deliver a potent natural healing experience.</h2>
    <p class="body-copy">At Fennow Roots Remedies, we understand that when d effective relief. That's why it is important to use the most gentle and proven herbs available.</p>
  </div>
</section>

<section class="screen" style="left:45px;top:750px;height:420px">
  <div class="photo" role="img" aria-label="Photo strip of a grey knit sweater" style="height:46px;background:linear-gradient(90deg,#4b4f55,#7a7f86)"></div>
  <div class="pad">
    <h2 class="h-sans">Experience the Difference That Expertise Makes!</h2>
    <p class="body-copy">Meet Elias, the creator of Fennow Roots Remedies. Inspired by his personal journey to heal his chronic pain, he devoted his life to studying medicinal plants and how to harness their healing abilities to improve the lives of others. As a trained herbalist, botanical medicine researcher and supplement formulator, let Elias's expertise guide you back to health and wellness.</p>
    <span class="btn">Read more</span>
  </div>
  <div class="faq" style="padding:18px 20px">
    <div class="faq__eyebrow"><span class="rule"></span>FAQ</div>
    <div class="faq__title">Ask us anything</div>
  </div>
</section>

<!-- Column 2 -->
<section class="screen" style="left:325px;top:40px;height:600px;background:var(--blue-5)">
  <div class="pad" style="display:flex;justify-content:space-between;align-items:center;background:var(--surface)">
    <div class="mini-brand"><i></i>Fennow Roots</div>
    <div class="menu"></div>
  </div>
  <div class="pad" style="padding-top:30px">
    <h1 class="hero-title">Welcome to Fennow Roots Remedies, where the wisdom of nature meets the art of healing.</h1>
    <span class="btn" style="margin-top:22px">Explore product</span>
  </div>
  <div role="img" aria-label="Bowl of green herbal powder on burlap with falling leaves" style="margin-top:auto;height:220px;background:linear-gradient(160deg,var(--blue-5) 0%,#cfe0d6 45%,#9bb58a 75%,#7c6a52 100%)"></div>
</section>

<section class="screen" style="left:325px;top:670px;height:500px">
  <div class="pad" style="padding:14px 20px 20px"><span class="btn" style="margin:0">Read more</span></div>
  <div class="faq">
    <div class="faq__eyebrow"><span class="rule"></span>FAQ</div>
    <div class="faq__title">Ask us anything</div>
    <div class="faq__sub">Have any questions? We're here to assist you.</div>
    <div class="faq__item"><div>✦ Does it work?<p>Absolutely! You will start to feel relief within 1 minute. After 15 minutes you will feel its full effects. At Fennow Roots Remedies, we stand by the effectiveness of our Pain Cream.</p></div><span class="icon">×</span></div>
    <div class="faq__item"><div>✦ Who is this natural pain relief cream for?</div><span class="icon">+</span></div>
    <div class="faq__item"><div>✦ How do I use it?</div><span class="icon">+</span></div>
  </div>
</section>

<!-- Column 3 -->
<section class="screen" style="left:605px;top:40px;height:520px">
  <div class="pad">
    <h2 class="h-sans">harvested from the wild and from the farm, to deliver a potent natural healing experience.</h2>
    <p class="body-copy">At Fennow Roots Remedies, we understand that when d effective relief. That's why it is important to use the most natural pain relief cream. Each ingredient reflects nature's finest.</p>
    <p class="body-copy" style="margin-top:10px">Try our <b>natural pain relief cream</b> and let the calming effect become your place of comfort and vitality.</p>
    <span class="btn">Explore the ingridients</span>
  </div>
  <div role="img" aria-label="Mountain landscape photo with a person wearing a cap" style="margin-top:auto;height:150px;background:linear-gradient(180deg,#c9d3da 0%,#9aa0a0 50%,#8a6a55 100%)"></div>
</section>

<section class="screen" style="left:605px;top:590px;height:580px">
  <div class="pad">
    <div class="mini-brand" style="font-size:16px"><i style="width:16px;height:16px"></i>Fennow Roots</div>
    <div style="font-size:11px;font-weight:700;color:var(--navy);margin-top:20px">Get Our Weekly Newsletter (Zero Spam)</div>
    <div class="field">Type In Your Email</div>
    <span class="btn" style="margin-top:10px">Send</span>
    <div class="nav-title">Navigation</div>
    <ul class="nav-list"><li>Home</li><li>Features</li><li>Market</li><li>Blog</li><li>Career</li></ul>
  </div>
</section>

<!-- Column 4 -->
<section class="screen" style="left:885px;top:40px;height:560px">
  <div role="img" aria-label="Portrait photo of the herbalist outdoors in the mountains" style="height:360px;background:linear-gradient(160deg,#b7c2c8 0%,#8f8a80 50%,#55585c 100%)"></div>
  <div class="pad">
    <h2 class="h-sans">Experience the Difference That Expertise Makes!</h2>
    <span class="btn" style="margin-top:4px">Read more</span>
  </div>
</section>

<section class="screen" style="left:885px;top:630px;height:540px">
  <div class="pad" style="padding-top:28px">
    <h2 class="h-sans" style="text-align:center">Start Your Journey With Us</h2>
    <p class="body-copy" style="text-align:center">Where The Wisdom Of Nature Meets The Art Of Healing.</p>
    <div class="field">Your Email</div>
    <div style="text-align:center"><span class="btn">Contact Us</span></div>
  </div>
  <div class="faq">
    <div class="faq__eyebrow"><span class="rule"></span>FAQ</div>
    <div class="faq__title">Ask us anything</div>
    <div class="faq__sub">Have any questions? We're here to assist you.</div>
    <div class="faq__item"><div>✦ Does it work?</div><span class="icon">+</span></div>
  </div>
</section>

</body>
</html>
```